Request for Business Card Design

Hi. My name is Marlene, I am looking for a new business card design for my company, Quarrow Signal Instruments, LLC. I really like the design you did for Tarsel Venture and was hoping you could do something similar using our full logo and our mark. I am also open to any raised texture design using our mark. I have attached our full logo, which would need to be somewhere on the card, as well as the mark in both outline and full form, as well as our brand colors / guide. The card does not have to be white, as long as our logo and mark appear. I actually like darker colored business cards more, but am open to all options. If you are interested in working with me, please let me know. We would also take the business card design into letterhead design if you can do that.

```html
<!DOCTYPE html>
<html lang="en">
<head>
<meta charset="utf-8">
<title>Quarrow Signal Instruments – Business Card</title>
<link href="https://fonts.googleapis.com/css2?family=Lato:wght@400;700&display=swap" rel="stylesheet">
<style>
  :root {
    --page-bg: #e6e4e2;
    --frost-light: #e4ebee;
    --frost-mid: #c3dbe3;
    --teal-light: #4d9fbb;
    --teal-deep: #0a6487;
    --teal-mid: #17779a;
    --teal-edge: #3a8ba7;
    --ink-light: #edf4f7;
    --ink-soft: #dbe9ef;
    --logo-grey: #4b5056;
    --logo-teal: #2f8aa6;
  }
  * { margin: 0; padding: 0; box-sizing: border-box; }
  html, body {
    width: 1200px; height: 734px; overflow: hidden;
    background: var(--page-bg);
    font-family: "Lato", sans-serif;
  }
  .canvas { position: relative; width: 1200px; height: 734px; }
  .business-card {
    position: absolute; left: 50px; top: 52px;
    width: 1100px; height: 630px;
    border-radius: 4px 36px 36px 4px;
    overflow: hidden;
    background: linear-gradient(90deg,
      var(--frost-light) 0%, var(--frost-mid) 32%,
      var(--teal-light) 46%, var(--teal-deep) 58%,
      var(--teal-mid) 82%, var(--teal-edge) 100%);
    box-shadow: 0 10px 30px rgba(0,0,0,0.15);
  }
  .mark-decoration {
    position: absolute; left: 0; top: 0; width: 540px; height: 630px;
    background: radial-gradient(ellipse at 45% 50%,
      rgba(255,255,255,0.55) 0%, rgba(220,236,242,0.35) 45%, rgba(160,205,220,0) 80%);
  }
  .brand {
    position: absolute; left: 52px; top: 283px;
    display: flex; align-items: center; gap: 22px;
  }
  .brand-dot { width: 84px; height: 84px; border-radius: 50%; background: var(--logo-teal); }
  .brand-name {
    font-weight: 700; font-size: 30px; line-height: 1.15;
    letter-spacing: 2px; color: var(--logo-grey);
  }
  .identity {
    position: absolute; right: 80px; top: 96px; text-align: right;
    color: var(--ink-light);
  }
  .identity-name { font-weight: 700; font-size: 52px; letter-spacing: 1px; line-height: 1.1; }
  .identity-title { font-weight: 400; font-size: 28px; margin-top: 2px; }
  .contact-list {
    position: absolute; right: 80px; top: 308px;
    list-style: none; color: var(--ink-soft);
    font-size: 25px; text-align: right;
  }
  .contact-item {
    display: flex; justify-content: flex-end; align-items: flex-start;
    gap: 20px; line-height: 39px;
  }
  .contact-icon { width: 22px; height: 39px; flex: none; display: flex; align-items: center; }
  .contact-icon svg { width: 22px; height: 22px; fill: none; stroke: var(--ink-soft); stroke-width: 2; }
</style>
</head>
<body>
<div class="canvas">
  <div class="business-card">
    <div class="mark-decoration" role="img" aria-label="Large faint brand mark decoration"></div>

    <div class="brand">
      <div class="brand-dot"></div>
      <div class="brand-name">QUARROW SIGNAL<br>INSTRUMENTS</div>
    </div>

    <div class="identity">
      <div class="identity-name">DORIAN FELL</div>
      <div class="identity-title">Founder &amp; CEO</div>
    </div>

    <ul class="contact-list">
      <li class="contact-item">
        <span>1180 Harlow Mill Road<br>Brenton, CO 80611</span>
        <span class="contact-icon"><svg viewBox="0 0 24 24"><path d="M12 22s7-7.2 7-12.5A7 7 0 0 0 5 9.5C5 14.8 12 22 12 22z"/><circle cx="12" cy="9.5" r="2.5"/></svg></span>
      </li>
      <li class="contact-item">
        <span>+001 555 210 4418</span>
        <span class="contact-icon"><svg viewBox="0 0 24 24"><path d="M5 3h4l2 5-3 2a12 12 0 0 0 6 6l2-3 5 2v4a2 2 0 0 1-2 2A18 18 0 0 1 3 5a2 2 0 0 1 2-2z"/></svg></span>
      </li>
      <li class="contact-item">
        <span>+001 555 210 7730</span>
        <span class="contact-icon"><svg viewBox="0 0 24 24"><rect x="7" y="3" width="10" height="5"/><rect x="3" y="8" width="18" height="9" rx="1"/><rect x="7" y="14" width="10" height="7"/></svg></span>
      </li>
      <li class="contact-item">
        <span>marlene@quarrowsignal.com</span>
        <span class="contact-icon"><svg viewBox="0 0 24 24"><rect x="3" y="5" width="18" height="14"/><path d="M3 5l9 8 9-8"/></svg></span>
      </li>
      <li class="contact-item">
        <span>www.quarrowsignal.com</span>
        <span class="contact-icon"><svg viewBox="0 0 24 24"><circle cx="12" cy="12" r="9"/><path d="M3 12h18M12 3c3 3 3 15 0 18M12 3c-3 3-3 15 0 18"/></svg></span>
      </li>
    </ul>
  </div>
</div>
</body>
</html>
```